RiverPine - Rebranding, Namecard, Stationary and One Page Web

Refresh logo, make it modern and design matching name card, stationary and one page web

RiverPine Information Technology (Int'l) Company Limited
松河訊息科技(國際)有限公司

Company is System Integrator, and will be providing products and services to government and enterprise organizations. Our Chief Security Officer came from top U.S. vendor, and had been working on top enterprise and government projects globally, so we want the refreshed image of the new company to have a East Cost U.S. style, with hint of technology from Silicon Valley. The company will also be representing top brands from the U.S. on information security.

Branding refresh is needed because company is being acquired and is expanding

Target Market(s)

Cyber Security

Industry/Entity Type

Information Technology

Contact Information for Business Card

Need Chinese and English

Number of Pages Required

1 page

Font styles to use
Sans Serif

Colors
0292cd
00a990

Requirements
Must have
• Modern, clean, cyber look. Must keep same colors and general look and feel of original logo. Only modernization, do not change its personality

```html
<!DOCTYPE html>
<html lang="en">
<head>
<meta charset="utf-8">
<title>RiverPine Name Card</title>
<link rel="stylesheet" href="https://fonts.googleapis.com/css2?family=Exo+2:wght@700&family=Open+Sans:wght@400;600&family=Noto+Sans+TC:wght@400&display=swap">
<style>
  :root {
    --brand-blue: #0292cd;
    --brand-blue-light: #27a8de;
    --brand-blue-deep: #0a86c4;
    --brand-teal: #00a990;
    --ink: #3c3c3c;
    --rule: #8a8a8a;
    --paper: #ffffff;
    --backdrop: #2a2a2a;
  }
  * { margin: 0; padding: 0; box-sizing: border-box; }
  html, body { width: 1200px; height: 1000px; overflow: hidden; }
  body {
    background: var(--backdrop);
    font-family: "Open Sans", Arial, sans-serif;
    position: relative;
  }
  .card {
    position: absolute;
    width: 600px;
    height: 343px;
    border-radius: 24px;
    overflow: hidden;
  }
  /* Front */
  .card-front {
    left: 110px; top: 110px;
    background: linear-gradient(135deg, var(--brand-blue-light) 0%, var(--brand-blue) 55%, var(--brand-blue-deep) 100%);
    color: var(--paper);
    display: flex;
    flex-direction: column;
    align-items: center;
    justify-content: center;
    text-align: center;
  }
  .wordmark {
    display: flex;
    align-items: center;
    gap: 10px;
    font-family: "Exo 2", Arial, sans-serif;
    font-weight: 700;
    letter-spacing: 1px;
  }
  .wordmark .dot { border-radius: 50%; flex: none; }
  .card-front .wordmark { font-size: 40px; color: var(--paper); }
  .card-front .wordmark .dot { width: 16px; height: 16px; background: var(--paper); }
  .company-en { margin-top: 40px; font-size: 13px; font-weight: 600; }
  .company-zh { margin-top: 2px; font-family: "Noto Sans TC", sans-serif; font-size: 12px; }

  /* Back */
  .card-back {
    left: 490px; top: 540px;
    background: var(--paper);
    color: var(--ink);
  }
  .card-back .wordmark {
    position: absolute; right: 36px; top: 44px;
    font-size: 34px; color: var(--brand-blue);
  }
  .card-back .wordmark .dot { width: 14px; height: 14px; background: var(--brand-blue); }
  .top-rule {
    position: absolute; left: 150px; right: 36px; top: 118px;
    height: 1px; background: var(--rule);
  }
  .address {
    position: absolute; right: 36px; top: 132px;
    text-align: right; font-size: 12px; line-height: 1.45;
  }
  .person { position: absolute; left: 40px; top: 170px; }
  .person-name {
    font-family: "Exo 2", Arial, sans-serif; font-weight: 700;
    font-size: 26px; color: var(--brand-blue); letter-spacing: 0.5px;
  }
  .person-title { font-size: 15px; margin-top: 2px; }
  .person-rule { width: 250px; height: 1px; background: var(--rule); margin-top: 6px; }
  .contacts { list-style: none; margin-top: 12px; }
  .contacts li {
    display: flex; align-items: center; gap: 12px;
    font-size: 13px; line-height: 22px;
  }
  .contacts svg { width: 12px; height: 12px; fill: var(--brand-blue-deep); flex: none; }
  .contacts .contact-text { white-space: nowrap; }
  .contacts .highlight { color: var(--brand-blue); }
  .base-band { position: absolute; left: 0; bottom: 0; width: 600px; height: 110px; }
</style>
</head>
<body>

<section class="card card-front" aria-label="Name card front">
  <div class="wordmark"><span class="dot"></span>RIVERPINE</div>
  <p class="company-en">RiverPine Information Technology (Int'l) Company Limited</p>
  <p class="company-zh">松河訊息科技(國際)有限公司</p>
</section>

<section class="card card-back" aria-label="Name card back">
  <div class="wordmark"><span class="dot"></span>RIVERPINE</div>
  <div class="top-rule"></div>
  <p class="address">
    Room B, Unit 402, 4/F, Lok Tin Ind. Bldg,<br>
    No. 15 Hing Wah Street, Kwun Tong,<br>
    Kowloon, HKSAR
  </p>

  <div class="person">
    <h1 class="person-name">DANIEL WONG</h1>
    <p class="person-title">CEO</p>
    <div class="person-rule"></div>
    <ul class="contacts">
      <li><svg viewBox="0 0 24 24"><path d="M6.6 10.8a15.1 15.1 0 0 0 6.6 6.6l2.2-2.2a1 1 0 0 1 1-.25 11.4 11.4 0 0 0 3.6.57 1 1 0 0 1 1 1V20a1 1 0 0 1-1 1A17 17 0 0 1 3 4a1 1 0 0 1 1-1h3.5a1 1 0 0 1 1 1c0 1.25.2 2.45.57 3.57a1 1 0 0 1-.25 1z"/></svg><span class="contact-text">(852) 5120 4417</span></li>
      <li><svg viewBox="0 0 24 24"><path d="M2 5h20v14H2z M2 5l10 8 10-8" /></svg><span class="contact-text">danielwong@riverpine-it.com.hk</span></li>
      <li><svg viewBox="0 0 24 24"><circle cx="12" cy="12" r="10"/></svg><span class="contact-text">www.<span class="highlight">riverpine-it</span>.com.hk</span></li>
    </ul>
  </div>

  <svg class="base-band" viewBox="0 0 600 110" preserveAspectRatio="none" aria-hidden="true">
    <path d="M0 100 L420 72 Q432 71 438 60 Q444 50 458 49 L600 40 L600 110 L0 110 Z" fill="var(--brand-teal)"/>
    <path d="M0 104 L420 76 Q432 75 438 64 Q444 54 458 53 L600 44 L600 110 L0 110 Z" fill="var(--brand-blue-deep)"/>
  </svg>
</section>

</body>
</html>
```